Dietitian needs awesome business card

I need a contemporary design that's eye catching but professional.
My card is to given to doctors, specialists and patients alike.
I manage patients with chronic diseases
I have uploaded my logo and current business card, I would also like the other Certified Clinical Nutritionist logo incorporated into the design

Target Market(s)

Doctors, specialists and patients

Industry/Entity Type

Healthcare

Contact Information for Business Card

www.brightfieldnutrition.com.au
Ph: 0427 561 903
Fax: 6457 2183
email: marcus.k.diet@fernmail.com
Space on the back of the card with: Appointment date, Appointment time and appointment location

Font styles to use
Serif

Colors
fbee3e
876aae
ffc214

Requirements
Must have
• My Logo
• Certified Clinical Nutritionist Logo
• My 4 locations - Pinebrook Medical Centre, North Corrin Health, Hollis Medical, Ashcombe Doctors Surgery
Nice to have
• I like the colours in my current business card

```html
<!DOCTYPE html>
<html lang="en">
<head>
<meta charset="utf-8">
<title>Brightfield Nutrition &amp; Dietetics — Business Card</title>
<link rel="stylesheet" href="https://fonts.googleapis.com/css2?family=Montserrat:wght@400;500;600&family=PT+Serif:wght@400;700&display=swap">
<style>
  :root {
    --backdrop: #2b2b2d;
    --card: #ffffff;
    --navy: #27338f;
    --green: #3db54a;
    --lime: #8cc63f;
    --orange: #f47a20;
    --faint: #eef4ea;
    --ink-line: #2a3a9a;
  }
  * { box-sizing: border-box; margin: 0; padding: 0; }
  html, body { width: 1200px; height: 900px; overflow: hidden; }
  body {
    background: var(--backdrop);
    position: relative;
    font-family: "Montserrat", sans-serif;
  }
  .card {
    position: absolute;
    width: 540px;
    height: 310px;
    background: var(--card);
    border-radius: 22px;
    overflow: hidden;
    box-shadow: 0 14px 30px rgba(0,0,0,.45);
  }

  /* ---------- appointment side ---------- */
  .card--front { left: 50px; top: 110px; }
  .front__watermark {
    position: absolute; left: 230px; top: 70px;
    width: 190px; height: 190px; border-radius: 50%;
    background: var(--faint);
  }
  .front__brand {
    position: absolute; left: 40px; top: 92px;
    display: flex; align-items: center; gap: 12px;
  }
  .brand-dot {
    width: 46px; height: 46px; border-radius: 50%;
    background: var(--green);
    flex: none;
  }
  .brand-name {
    font-family: "Montserrat", sans-serif;
    font-weight: 600;
    font-size: 21px;
    line-height: 1.15;
    color: var(--navy);
    width: 250px;
  }
  .front__badge {
    position: absolute; right: 40px; top: 26px;
    width: 110px; height: 44px;
    background: var(--orange);
    border-radius: 3px;
  }
  .appointment {
    position: absolute; left: 40px; top: 178px; right: 40px;
    color: var(--navy);
    font-size: 15px;
    font-weight: 500;
  }
  .appointment__title {
    color: var(--green);
    font-weight: 600;
    font-size: 18px;
    margin-bottom: 10px;
  }
  .appointment__row { display: flex; gap: 14px; margin-bottom: 16px; }
  .field { display: flex; align-items: flex-end; flex: 1; gap: 6px; }
  .field__line { flex: 1; border-bottom: 1.5px solid var(--ink-line); height: 18px; }

  /* ---------- contact side ---------- */
  .card--back { left: 610px; top: 470px; }
  .back__mark {
    position: absolute; left: 30px; top: 60px;
    width: 170px; height: 170px;
    display: flex; flex-direction: column; align-items: center; justify-content: center; gap: 10px;
  }
  .back__mark .brand-dot { width: 70px; height: 70px; }
  .back__mark .brand-name { width: 170px; text-align: center; font-size: 16px; }
  .back__divider {
    position: absolute; left: 215px; top: 40px;
    width: 1.5px; height: 150px; background: var(--navy);
  }
  .person {
    position: absolute; left: 236px; top: 40px;
  }
  .person__name {
    font-family: "PT Serif", serif;
    font-size: 24px;
    color: var(--navy);
    margin-bottom: 8px;
  }
  .person__name span { color: var(--green); }
  .contact-list { list-style: none; font-size: 14px; color: var(--navy); }
  .contact-list li { display: flex; align-items: center; gap: 8px; line-height: 22px; }
  .contact-list svg { width: 11px; height: 11px; flex: none; }
  .back__band {
    position: absolute; left: 0; right: 0; bottom: 34px;
    height: 22px; background: var(--green);
  }
  .back__tag {
    position: absolute; left: 150px; right: 30px; bottom: 26px;
    height: 38px;
    background: var(--navy);
    border-radius: 8px;
    border: 2px solid #fff;
    color: #fff;
    font-family: "PT Serif", serif;
    font-size: 15px;
    display: flex; align-items: center; justify-content: center;
  }
</style>
</head>
<body>

  <section class="card card--front" aria-label="Appointment side">
    <div class="front__watermark" aria-hidden="true"></div>
    <div class="front__brand">
      <span class="brand-dot"></span>
      <span class="brand-name">Brightfield Nutrition &amp; Dietetics</span>
    </div>
    <div class="front__badge" role="img" aria-label="Accreditation badge"></div>
    <div class="appointment">
      <p class="appointment__title">Appointment:</p>
      <div class="appointment__row">
        <div class="field">Date:<span class="field__line"></span></div>
        <div class="field">Time:<span class="field__line"></span></div>
      </div>
      <div class="appointment__row">
        <div class="field">Location:<span class="field__line"></span></div>
      </div>
    </div>
  </section>

  <section class="card card--back" aria-label="Contact side">
    <div class="back__mark">
      <span class="brand-dot"></span>
      <span class="brand-name">Brightfield Nutrition &amp; Dietetics</span>
    </div>
    <div class="back__divider"></div>
    <div class="person">
      <h1 class="person__name">Marcus <span>Kellbrook</span></h1>
      <ul class="contact-list">
        <li>
          <svg viewBox="0 0 12 12"><path d="M2 1l2.2 0 .8 2.6-1.3 1a6 6 0 0 0 2.7 2.7l1-1.3 2.6.8V10c0 .6-.5 1-1 1A9 9 0 0 1 1 2c0-.5.4-1 1-1z" fill="var(--green)"/></svg>
          0427 561 903
        </li>
        <li>
          <svg viewBox="0 0 12 12"><rect x="1" y="4" width="10" height="6" rx="1" fill="var(--green)"/><rect x="3" y="1" width="6" height="3" fill="var(--green)"/></svg>
          6457 2183
        </li>
        <li>
          <svg viewBox="0 0 12 12"><rect x="1" y="2.5" width="10" height="7" rx="1" fill="none" stroke="var(--green)" stroke-width="1.3"/><path d="M1.5 3l4.5 3.5L10.5 3" fill="none" stroke="var(--green)" stroke-width="1.3"/></svg>
          marcus.k.diet@fernmail.com
        </li>
        <li>
          <svg viewBox="0 0 12 12"><circle cx="6" cy="6" r="4.8" fill="none" stroke="var(--green)" stroke-width="1.3"/><path d="M1.2 6h9.6M6 1.2c-2.4 3-2.4 6.6 0 9.6M6 1.2c2.4 3 2.4 6.6 0 9.6" fill="none" stroke="var(--green)" stroke-width="1"/></svg>
          www.brightfieldnutrition.com.au
        </li>
      </ul>
    </div>
    <div class="back__band"></div>
    <div class="back__tag">Certified Clinical Nutritionist, Nutrionist and Chef</div>
  </section>

</body>
</html>
```